Tinned Food Label Design

We are after 5 Labels for tinned food
1: Diced Tomato's 425g
2: Baked Beans 425g
3: Two Fruits (Peach & Pear) 820g
4: Sliced Peaches 820g
5: Mixed Vegetables (Peas, Carrots and Corn) 425g

we will supply Nutritional Information per product
Importers Name and address must be included.
Imported By: Bell & Quarry PTY LTD
Unit 8 / 32 Petherick Ave
Marlow Bay QLD 4187

also in a Square Box: Made in China

similar to attached Label uploaded. I will also send Die lines to use for designs. The Brand Name is NOT KOLM this is just example of the Label Type Brand is WREN Meadow

Target Market(s)

Supermarkets

Industry/Entity Type

Food

Requirements
Must have
• Image and Product Description

```html
<!DOCTYPE html>
<html lang="en">
<head>
<meta charset="utf-8">
<title>WREN Meadow – Tinned Food Labels</title>
<link href="https://fonts.googleapis.com/css2?family=Arimo:wght@400;700&family=Lilita+One&family=Source+Sans+3:wght@400;700&display=swap" rel="stylesheet">
<style>
:root{
  --sheet:#ffffff;
  --guide:#e0303a;
  --label-top:#000000;
  --label-mid:#1b0607;
  --label-bottom:#5a2c12;
  --brand-red:#b8182c;
  --ribbon:#c81a30;
  --ribbon-dark:#8a0f1f;
  --cream:#f6e3b4;
  --text:#ffffff;
  --text-soft:#e9dcd0;
}
*{box-sizing:border-box;margin:0;padding:0}
html,body{width:1200px;height:2847px;overflow:hidden;background:var(--sheet)}
body{position:relative;font-family:"Arimo",Arial,sans-serif}
.dieline{position:absolute;left:0;width:1200px;height:553px}
.dim-h{position:absolute;left:105px;width:975px;top:-33px;height:1px;background:var(--guide)}
.dim-h::before,.dim-h::after{content:"";position:absolute;top:-4px;border:4px solid transparent}
.dim-h::before{left:-4px;border-right:6px solid var(--guide);border-left:0}
.dim-h::after{right:-4px;border-left:6px solid var(--guide);border-right:0}
.dim-h-label{position:absolute;left:50%;top:-12px;transform:translateX(-50%);background:var(--sheet);padding:0 4px;color:var(--guide);font-style:italic;font-size:13px}
.dim-v{position:absolute;left:50px;top:20px;height:397px;width:1px;background:var(--guide)}
.dim-v::before,.dim-v::after{content:"";position:absolute;left:-4px;border:4px solid transparent}
.dim-v::before{top:-4px;border-bottom:6px solid var(--guide);border-top:0}
.dim-v::after{bottom:-4px;border-top:6px solid var(--guide);border-bottom:0}
.dim-v-label{position:absolute;left:-8px;top:50%;transform:translate(-50%,-50%) rotate(-90deg);background:var(--sheet);padding:0 4px;color:var(--guide);font-style:italic;font-size:13px;white-space:nowrap}
.seam-mark{position:absolute;left:1031px;top:-22px;width:1px;height:22px;background:#c9c9c9}

.label{position:absolute;left:83px;top:0;width:1022px;height:435px;border:1px solid var(--guide);
  background:linear-gradient(180deg,var(--label-top) 0%,var(--label-mid) 45%,var(--label-bottom) 100%);overflow:hidden}
.safe{position:absolute;left:20px;top:18px;width:928px;height:399px;border:1px dashed var(--guide)}
.overlap{position:absolute;left:965px;top:18px;width:57px;height:399px;border-left:1px dashed var(--guide);border-top:1px dashed var(--guide)}
.glue{position:absolute;left:948px;top:0;width:0;height:435px;border-left:1px dashed var(--guide)}
.front-rule{position:absolute;top:0;width:4px;height:435px;background:var(--brand-red)}
.front-rule.left{left:393px}.front-rule.right{left:631px}

.importer{position:absolute;left:82px;top:44px;width:200px;text-align:center;color:var(--text);font-weight:700;font-size:13px;line-height:15.5px}
.origin{display:inline-block;margin-top:10px;border:1px solid var(--text);padding:1px 7px;font-size:11.5px;line-height:14px;font-weight:700}
.recycle{display:block;margin:9px auto 0;width:40px;height:38px}
.recycle-note{font-size:5px;letter-spacing:.3px;line-height:6px}

.brand{position:absolute;left:397px;top:52px;width:234px;text-align:center;font-family:"Lilita One",sans-serif;color:var(--cream);font-size:38px;line-height:38px;letter-spacing:2px}
.ribbon{position:absolute;left:369px;top:180px;width:290px;height:64px}
.ribbon svg{position:absolute;inset:0}
.product-name{position:absolute;left:22px;right:22px;top:10px;text-align:center;font-family:"Lilita One",sans-serif;color:var(--text);font-size:25px;line-height:34px;white-space:nowrap;text-shadow:0 1px 2px rgba(0,0,0,.5)}
.photo{position:absolute;left:397px;top:238px;width:234px;height:197px}
.variety{position:absolute;left:397px;top:240px;width:234px;text-align:center;font-family:"Lilita One",sans-serif;color:var(--text);font-size:16px;z-index:2;
  text-shadow:0 0 2px #5a0d14,0 0 2px #5a0d14,0 1px 3px #5a0d14}
.weight{position:absolute;right:398px;bottom:8px;font-family:"Arimo",Arial,sans-serif;font-weight:700;color:var(--text);font-size:16px;z-index:2;text-shadow:0 1px 3px rgba(0,0,0,.7)}
.photo.veg{background:linear-gradient(135deg,#5f9e2c 0%,#e8b622 35%,#e8702a 55%,#86b83c 80%,#d9a52a 100%)}
.photo.peach{background:linear-gradient(150deg,#e9a43a 0%,#f6c85a 35%,#e3672b 60%,#f2b44a 100%)}
.photo.pear{background:linear-gradient(160deg,#5c5a3a 0%,#d8cb7c 35%,#e57a4a 55%,#c83d36 70%,#6b5544 100%)}
.photo.tomato{background:linear-gradient(170deg,#5e140c 0%,#d0301c 35%,#e2543a 55%,#9a5c3a 80%,#5a3a28 100%)}
.photo.beans{background:linear-gradient(170deg,#3a2a22 0%,#5b4436 35%,#b8542a 60%,#6a5646 100%)}

.panel{position:absolute;left:687px;top:52px;width:243px;color:var(--text);font-family:"Source Sans 3",Arial,sans-serif}
.nutrition{width:100%;table-layout:fixed;border:1.5px solid var(--text);border-collapse:collapse;font-size:8.5px;line-height:14px}
.nutrition td{padding:0 7px;vertical-align:bottom;white-space:nowrap}
.nutrition .title td{font-weight:700;font-size:8.5px;border-bottom:1px solid var(--text)}
.nutrition .num{text-align:right}
.nutrition .sep{text-align:left;padding-left:8px}
.nutrition .meta.last td{border-bottom:1px solid var(--text)}
.nutrition .heads td{text-align:right;line-height:10.5px;padding-top:6px;padding-bottom:2px;border-bottom:1px solid var(--text);padding-left:2px}
.nutrition .div{border-left:1px solid var(--text)}
.nutrition .c1{width:53%}
.nutrition .c2,.nutrition .c3{width:23.5%}
.nutrition.four .c1{width:36%}
.nutrition.four .c2,.nutrition.four .c3,.nutrition.four .c4{width:21.3%}
.nutrition.four td{padding:0 5px}
.notes{font-size:9px;line-height:12px;margin-top:12px;color:var(--text-soft)}
.notes p{margin-bottom:9px}
.notes b{color:var(--text)}
</style>
</head>
<body>

<!-- Mixed Vegetables -->
<section class="dieline" style="top:70px">
  <div class="dim-h"><span class="dim-h-label">245 mm</span></div>
  <div class="dim-v"><span class="dim-v-label">102 mm</span></div>
  <div class="seam-mark"></div>
  <article class="label">
    <div class="safe"></div><div class="glue"></div><div class="overlap"></div>
    <div class="front-rule left"></div><div class="front-rule right"></div>
    <div class="importer">Imported By:<br>Bell &amp; Quarry PTY LTD<br>Unit 8 / 32 Petherick Ave<br>Marlow Bay QLD 4187<br><span class="origin">Made in China</span>
      <svg class="recycle" viewBox="0 0 40 38" aria-hidden="true"><g fill="none" stroke="#fff" stroke-width="4"><path d="M9 26 A12 12 0 0 1 14 8"/><path d="M22 6 A12 12 0 0 1 32 20"/><path d="M28 30 A12 12 0 0 1 12 31"/></g><g fill="#fff"><path d="M10 4 L20 6 L13 13Z"/><path d="M34 14 L31 25 L26 18Z"/><path d="M14 36 L6 28 L15 26Z"/></g></svg>
      <div class="recycle-note">PLEASE RECYCLE</div></div>
    <div class="brand">WREN<br>MEADOW</div>
    <div class="ribbon"><svg viewBox="0 0 290 64"><polygon points="0,24 34,24 34,58 0,58 11,41" fill="var(--ribbon-dark)"/><polygon points="290,24 256,24 256,58 290,58 279,41" fill="var(--ribbon-dark)"/><path d="M22 12 Q145 -2 268 12 L268 48 Q145 34 22 48Z" fill="var(--ribbon)"/></svg><div class="product-name">Mixed Vegetables</div></div>
    <div class="variety">Peas · Carrots · Corn</div>
    <div class="photo veg" role="img" aria-label="Photo of mixed peas, diced carrots and corn kernels"></div>
    <div class="weight">425g</div>
    <div class="panel">
      <table class="nutrition">
        <colgroup><col class="c1"><col class="c2"><col class="c3"></colgroup>
        <tr class="title"><td colspan="3">NUTRITION INFORMATION</td></tr>
        <tr class="meta"><td>Servings per package</td><td class="sep">:</td><td class="num">3.5</td></tr>
        <tr class="meta last"><td>Serving size</td><td class="sep">:</td><td class="num">125g</td></tr>
        <tr class="heads"><td></td><td>Avg<br>Quantity per<br>Serve</td><td>Avg<br>Quantity per<br>100g</td></tr>
        <tr><td>Energy</td><td class="num div">188kJ</td><td class="num">150kJ</td></tr>
        <tr><td>Protein</td><td class="num div">3g</td><td class="num">2.4g</td></tr>
        <tr><td>Fat, total</td><td class="num div">0g</td><td class="num">0g</td></tr>
        <tr><td>- saturated</td><td class="num div">0g</td><td class="num">0g</td></tr>
        <tr><td>Carbohydrate</td><td class="num div">9g</td><td class="num">7.2g</td></tr>
        <tr><td>- sugars</td><td class="num div">4g</td><td class="num">3.2g</td></tr>
        <tr><td>Sodium</td><td class="num div">290mg</td><td class="num">290mg</td></tr>
      </table>
      <div class="notes">
        <p>*Percentage of recommended dietary intake.</p>
        <p><b>Ingredients:</b><br>Green Peas, Carrots, Seet Corn, Water, Salt.</p>
        <p><b>Storage Instructions:</b><br>Store at room temperature in a cool, dry place and away from heat sources. Once opened, store in a refrigerator in a non-metallic container and consume within 3-4 days.</p>
      </div>
    </div>
  </article>
</section>

<!-- Sliced Peaches -->
<section class="dieline" style="top:623px">
  <div class="dim-h"><span class="dim-h-label">245 mm</span></div>
  <div class="dim-v"><span class="dim-v-label">102 mm</span></div>
  <div class="seam-mark"></div>
  <article class="label">
    <div class="safe"></div><div class="glue"></div><div class="overlap"></div>
    <div class="front-rule left"></div><div class="front-rule right"></div>
    <div class="importer">Imported By:<br>Bell &amp; Quarry PTY LTD<br>Unit 8 / 32 Petherick Ave<br>Marlow Bay QLD 4187<br><span class="origin">Made in China</span>
      <svg class="recycle" viewBox="0 0 40 38" aria-hidden="true"><g fill="none" stroke="#fff" stroke-width="4"><path d="M9 26 A12 12 0 0 1 14 8"/><path d="M22 6 A12 12 0 0 1 32 20"/><path d="M28 30 A12 12 0 0 1 12 31"/></g><g fill="#fff"><path d="M10 4 L20 6 L13 13Z"/><path d="M34 14 L31 25 L26 18Z"/><path d="M14 36 L6 28 L15 26Z"/></g></svg>
      <div class="recycle-note">PLEASE RECYCLE</div></div>
    <div class="brand">WREN<br>MEADOW</div>
    <div class="ribbon"><svg viewBox="0 0 290 64"><polygon points="0,24 34,24 34,58 0,58 11,41" fill="var(--ribbon-dark)"/><polygon points="290,24 256,24 256,58 290,58 279,41" fill="var(--ribbon-dark)"/><path d="M22 12 Q145 -2 268 12 L268 48 Q145 34 22 48Z" fill="var(--ribbon)"/></svg><div class="product-name">Sliced Peaches</div></div>
    <div class="photo peach" role="img" aria-label="Photo of sliced yellow peaches"></div>
    <div class="weight">820g</div>
    <div class="panel">
      <table class="nutrition">
        <colgroup><col class="c1"><col class="c2"><col class="c3"></colgroup>
        <tr class="title"><td colspan="3">NUTRITION INFORMATION</td></tr>
        <tr class="meta"><td>Servings per package</td><td class="sep">:</td><td class="num">Approx. 7</td></tr>
        <tr class="meta last"><td>Serving size</td><td class="sep">:</td><td class="num">125g</td></tr>
        <tr class="heads"><td></td><td>Avg<br>Quantity per<br>Serve</td><td>Avg<br>Quantity per<br>100g</td></tr>
        <tr><td>Energy</td><td class="num div">280kJ</td><td class="num">224kJ</td></tr>
        <tr><td>Protein</td><td class="num div">&lt;1g</td><td class="num">&lt;1g</td></tr>
        <tr><td>Fat, total</td><td class="num div">&lt;1g</td><td class="num">&lt;1g</td></tr>
        <tr><td>- saturated</td><td class="num div">&lt;1g</td><td class="num">&lt;1g</td></tr>
        <tr><td>Carbohydrate</td><td class="num div">15g</td><td class="num">12g</td></tr>
        <tr><td>- sugars</td><td class="num div">11.9g</td><td class="num">9.5g</td></tr>
        <tr><td>Sodium</td><td class="num div">&gt;5mg</td><td class="num">&gt;5mg</td></tr>
      </table>
      <div class="notes">
        <p><b>Allergen Information:</b><br>May contain traces of Barley, Milk, Soy made in factory that produces nut cookies.</p>
        <p><b>Ingredients:</b><br>Peach, Water, Sugar.</p>
        <p><b>Storage Instructions:</b><br>Store at room temperature in a cool, dry place and away from heat sources. Once opened, store in a refrigerator in a non-metallic container and consume within 3-4 days.</p>
      </div>
    </div>
  </article>
</section>

<!-- Two Fruits -->
<section class="dieline" style="top:1176px">
  <div class="dim-h"><span class="dim-h-label">245 mm</span></div>
  <div class="dim-v"><span class="dim-v-label">102 mm</span></div>
  <div class="seam-mark"></div>
  <article class="label">
    <div class="safe"></div><div class="glue"></div><div class="overlap"></div>
    <div class="front-rule left"></div><div class="front-rule right"></div>
    <div class="importer">Imported By:<br>Bell &amp; Quarry PTY LTD<br>Unit 8 / 32 Petherick Ave<br>Marlow Bay QLD 4187<br><span class="origin">Made in China</span>
      <svg class="recycle" viewBox="0 0 40 38" aria-hidden="true"><g fill="none" stroke="#fff" stroke-width="4"><path d="M9 26 A12 12 0 0 1 14 8"/><path d="M22 6 A12 12 0 0 1 32 20"/><path d="M28 30 A12 12 0 0 1 12 31"/></g><g fill="#fff"><path d="M10 4 L20 6 L13 13Z"/><path d="M34 14 L31 25 L26 18Z"/><path d="M14 36 L6 28 L15 26Z"/></g></svg>
      <div class="recycle-note">PLEASE RECYCLE</div></div>
    <div class="brand">WREN<br>MEADOW</div>
    <div class="ribbon"><svg viewBox="0 0 290 64"><polygon points="0,24 34,24 34,58 0,58 11,41" fill="var(--ribbon-dark)"/><polygon points="290,24 256,24 256,58 290,58 279,41" fill="var(--ribbon-dark)"/><path d="M22 12 Q145 -2 268 12 L268 48 Q145 34 22 48Z" fill="var(--ribbon)"/></svg><div class="product-name" style="font-size:29px">Two Fruits</div></div>
    <div class="variety">Peach &amp; Pear</div>
    <div class="photo pear" role="img" aria-label="Photo of whole and halved pears and peaches on a wooden table"></div>
    <div class="weight">820g</div>
    <div class="panel" style="top:48px">
      <table class="nutrition">
        <colgroup><col class="c1"><col class="c2"><col class="c3"></colgroup>
        <tr class="title"><td colspan="3">NUTRITION INFORMATION</td></tr>
        <tr class="meta"><td>Servings per package</td><td class="sep">:</td><td class="num">4</td></tr>
        <tr class="meta last"><td>Serving size</td><td class="sep">:</td><td class="num">115g</td></tr>
        <tr class="heads"><td></td><td>Avg<br>Quantity per<br>Serve</td><td>Avg<br>Quantity per<br>100g</td></tr>
        <tr><td>Energy</td><td class="num div">69kJ</td><td class="num">60kJ</td></tr>
        <tr><td>Protein</td><td class="num div">0g</td><td class="num">0g</td></tr>
        <tr><td>Fat, total</td><td class="num div">0g</td><td class="num">0g</td></tr>
        <tr><td>- saturated</td><td class="num div">0g</td><td class="num">0g</td></tr>
        <tr><td>Carbohydrate, total</td><td class="num div">20g</td><td class="num">20g</td></tr>
        <tr><td>- dietary fibers</td><td class="num div">1.15g</td><td class="num">1g</td></tr>
        <tr><td>- sugars</td><td class="num div">20.7g</td><td class="num">18g</td></tr>
        <tr><td>Sodium</td><td class="num div">23mg</td><td class="num">20mg</td></tr>
      </table>
      <div class="notes">
        <p>*Percentage of recommended dietary intake.</p>
        <p><b>Ingredients:</b><br>Pear, Yellow Peach, Water, Pear Juice Concentrate, Citric Acid.</p>
        <p><b>Storage Instructions:</b><br>Store at room temperature in a cool, dry place and away from heat sources. Once opened, store in a refrigerator in a non-metallic container and consume within 3-4 days.</p>
      </div>
    </div>
  </article>
</section>

<!-- Diced Tomatoes -->
<section class="dieline" style="top:1729px">
  <div class="dim-h"><span class="dim-h-label">245 mm</span></div>
  <div class="dim-v"><span class="dim-v-label">102 mm</span></div>
  <div class="seam-mark"></div>
  <article class="label">
    <div class="safe"></div><div class="glue"></div><div class="overlap"></div>
    <div class="front-rule left"></div><div class="front-rule right"></div>
    <div class="importer">Imported By:<br>Bell &amp; Quarry PTY LTD<br>Unit 8 / 32 Petherick Ave<br>Marlow Bay QLD 4187<br><span class="origin">Made in China</span>
      <svg class="recycle" viewBox="0 0 40 38" aria-hidden="true"><g fill="none" stroke="#fff" stroke-width="4"><path d="M9 26 A12 12 0 0 1 14 8"/><path d="M22 6 A12 12 0 0 1 32 20"/><path d="M28 30 A12 12 0 0 1 12 31"/></g><g fill="#fff"><path d="M10 4 L20 6 L13 13Z"/><path d="M34 14 L31 25 L26 18Z"/><path d="M14 36 L6 28 L15 26Z"/></g></svg>
      <div class="recycle-note">PLEASE RECYCLE</div></div>
    <div class="brand">WREN<br>MEADOW</div>
    <div class="ribbon"><svg viewBox="0 0 290 64"><polygon points="0,24 34,24 34,58 0,58 11,41" fill="var(--ribbon-dark)"/><polygon points="290,24 256,24 256,58 290,58 279,41" fill="var(--ribbon-dark)"/><path d="M22 12 Q145 -2 268 12 L268 48 Q145 34 22 48Z" fill="var(--ribbon)"/></svg><div class="product-name">Diced Tomato's</div></div>
    <div class="photo tomato" role="img" aria-label="Photo of whole and diced tomatoes on a chopping board"></div>
    <div class="weight">425g</div>
    <div class="panel">
      <table class="nutrition">
        <colgroup><col class="c1"><col class="c2"><col class="c3"></colgroup>
        <tr class="title"><td colspan="3">NUTRITION INFORMATION</td></tr>
        <tr class="meta"><td>Servings per package</td><td class="sep">:</td><td class="num">4</td></tr>
        <tr class="meta last"><td>Serving size</td><td class="sep">:</td><td class="num">57.5g</td></tr>
        <tr class="heads"><td></td><td>Avg<br>Quantity<br>per Serve</td><td>Avg<br>Quantity<br>per 100g</td></tr>
        <tr><td>Energy</td><td class="num div">59.2kJ</td><td class="num">103kJ</td></tr>
        <tr><td>Protein</td><td class="num div">0.86g</td><td class="num">1.5g</td></tr>
        <tr><td>Fat, total</td><td class="num div">0g</td><td class="num">0g</td></tr>
        <tr><td>- saturated</td><td class="num div">0g</td><td class="num">0g</td></tr>
        <tr><td>Carbohydrate, total</td><td class="num div">2.53g</td><td class="num">4.4g</td></tr>
        <tr><td>- sugars</td><td class="num div">0g</td><td class="num">0g</td></tr>
        <tr><td>Sodium</td><td class="num div">74.75mg</td><td class="num">130mg</td></tr>
      </table>
      <div class="notes">
        <p>*Percentage of recommended dietary intake.</p>
        <p><b>Ingredients:</b><br>Tomatoes (54%), Salt, Water.</p>
        <p><b>Storage Instructions:</b><br>Store at room temperature in a cool, dry place and away from heat sources. Once opened, store in a refrigerator in a non-metallic container and consume within 3-4 days.</p>
      </div>
    </div>
  </article>
</section>

<!-- Baked Beans -->
<section class="dieline" style="top:2282px">
  <div class="dim-h"><span class="dim-h-label">245 mm</span></div>
  <div class="dim-v"><span class="dim-v-label">102 mm</span></div>
  <div class="seam-mark"></div>
  <article class="label">
    <div class="safe"></div><div class="glue"></div><div class="overlap"></div>
    <div class="front-rule left"></div><div class="front-rule right"></div>
    <div class="importer">Imported By:<br>Bell &amp; Quarry PTY LTD<br>Unit 8 / 32 Petherick Ave<br>Marlow Bay QLD 4187<br><span class="origin">Made in China</span>
      <svg class="recycle" viewBox="0 0 40 38" aria-hidden="true"><g fill="none" stroke="#fff" stroke-width="4"><path d="M9 26 A12 12 0 0 1 14 8"/><path d="M22 6 A12 12 0 0 1 32 20"/><path d="M28 30 A12 12 0 0 1 12 31"/></g><g fill="#fff"><path d="M10 4 L20 6 L13 13Z"/><path d="M34 14 L31 25 L26 18Z"/><path d="M14 36 L6 28 L15 26Z"/></g></svg>
      <div class="recycle-note">PLEASE RECYCLE</div></div>
    <div class="brand">WREN<br>MEADOW</div>
    <div class="ribbon"><svg viewBox="0 0 290 64"><polygon points="0,24 34,24 34,58 0,58 11,41" fill="var(--ribbon-dark)"/><polygon points="290,24 256,24 256,58 290,58 279,41" fill="var(--ribbon-dark)"/><path d="M22 12 Q145 -2 268 12 L268 48 Q145 34 22 48Z" fill="var(--ribbon)"/></svg><div class="product-name">Baked Beans</div></div>
    <div class="photo beans" role="img" aria-label="Photo of baked beans in a cast iron pan on burlap"></div>
    <div class="weight">425g</div>
    <div class="panel">
      <table class="nutrition four">
        <colgroup><col class="c1"><col class="c2"><col class="c3"><col class="c4"></colgroup>
        <tr class="title"><td colspan="4">NUTRITION INFORMATION</td></tr>
        <tr class="meta"><td colspan="2">Servings per package</td><td class="sep">:</td><td class="num">2</td></tr>
        <tr class="meta last"><td colspan="2">Serving size</td><td class="sep">:</td><td class="num">200g</td></tr>
        <tr class="heads"><td></td><td>Avg<br>Quantity<br>per Serve</td><td>%Daily<br>Intake*<br>per Serve</td><td>Avg<br>Quantity<br>per 100g</td></tr>
        <tr><td>Energy</td><td class="num div">824kJ</td><td class="num">9.3%</td><td class="num">412kJ</td></tr>
        <tr><td>Protein</td><td class="num div">11.4g</td><td class="num">22.8%</td><td class="num">5.7g</td></tr>
        <tr><td>Fat, total</td><td class="num div">1.0g</td><td class="num">1.4%</td><td class="num">0.5g</td></tr>
        <tr><td>- saturated</td><td class="num div">0.2g</td><td class="num">0.8%</td><td class="num">0.1g</td></tr>
        <tr><td>Carbohydrate</td><td class="num div">30.6g</td><td class="num">9.9%</td><td class="num">15.3g</td></tr>
        <tr><td>- sugars</td><td class="num div">8.2g</td><td class="num">9.1%</td><td class="num">4.1g</td></tr>
        <tr><td>Sodium</td><td class="num div">424mg</td><td class="num">18.4%</td><td class="num">212mg</td></tr>
      </table>
      <div class="notes" style="margin-top:8px">
        <p style="margin-bottom:4px">*Percentage Daily Intakes are based on an average adult diet 8700kJ. Your daily intakes may be higher or lower depending on your energy needs.</p>
        <p style="margin-bottom:4px"><b>Ingredients:</b><br>Navy Beans (50%), Tomatoes (31%), Water, Sugar, Modified Maize Starch, Salt Spirit Vinegar, Ascorbic Acid, Natural Flavours.</p>
        <p><b>Storage Instructions:</b><br>Store at room temperature in a cool, dry place and away from heat sources. Once opened, store in a refrigerator in a non-metallic container and consume within 3-4 days.</p>
      </div>
    </div>
  </article>
</section>

</body>
</html>
```